Eye catching Bottle label for pink gin targeting women 25+

We need a new label for a re-launch of our shimmering strawberry pink gin liqueur. We would like it to look premium and eye catching on the shelf. We have 2 labels we require, one for 200ml bottle (2x2 inches) and one for 500ml bottle 4x4 inches). Label must state the ml of the bottle abd that it is 18.75%Vol. Also say Shimmering Strawberry Gin Liqueur with the brand name at the top - Tallow Crane. We have a logo but it doesn't need to be used if it doesn't work with the design/colours. The gin is presented in a clear bottle and is pink and sparkly. See uploaded image for reference.

Target Market(s)

Women aged 25-45

Font styles to use
Decorative

Colors
f59296
fbd4d5
eea4c8

Requirements
Must have
• Bottle size - 500ml/200ml
• Must say 18.75% Vol
• Must have brand name - Tallow Crane
• Must have product name - Glittering Rose Raspberry
• Must say - Gin Liqueur
Nice to have
• Some sort of floral or swirley background detail would be nice
Should not have
• Must not appeal to children

```html
<!DOCTYPE html>
<html lang="en">
<head>
<meta charset="utf-8">
<title>Glittering Rose Raspberry Gin Liqueur – Label</title>
<link rel="stylesheet" href="https://fonts.googleapis.com/css2?family=Lobster&family=Oswald:wght@500;600&family=Oranienbaum&display=swap">
<style>
  :root {
    --page: #f6f6f6;
    --label-light: #f4e4e3;
    --label-mid: #ecd2d0;
    --blush: #dcaeab;
    --rose: #c08582;
    --wine: #9a5a5b;
    --ink: #24160f;
    --gold: #c9962e;
    --gold-light: #e8c462;
  }
  * { margin: 0; padding: 0; box-sizing: border-box; }
  html, body { width: 900px; height: 1200px; overflow: hidden; background: var(--page); }
  .canvas { position: relative; width: 900px; height: 1200px; }

  .label {
    position: absolute; left: 140px; top: 120px; width: 620px; height: 960px;
    overflow: hidden;
    background: linear-gradient(160deg, var(--label-light) 0%, var(--label-mid) 55%, var(--blush) 100%);
  }
  .brush-band {
    position: absolute; left: 0; top: 0; width: 620px; height: 960px;
    background: linear-gradient(172deg, rgba(192,133,130,0) 55%, rgba(192,133,130,.5) 70%, var(--rose) 84%, rgba(154,90,91,.75) 100%);
  }
  .ornament-top {
    position: absolute; right: 0; top: 0; width: 380px; height: 420px;
    background: radial-gradient(ellipse at 80% 20%, rgba(201,150,46,.22), rgba(201,150,46,0) 65%);
  }
  .ornament-bottom {
    position: absolute; left: 0; top: 520px; width: 260px; height: 440px;
    background: radial-gradient(ellipse at 15% 55%, rgba(201,150,46,.25), rgba(201,150,46,0) 65%);
  }
  .rules { position: absolute; inset: 0; }

  .brand {
    position: absolute; left: 0; width: 620px; top: 182px; text-align: center;
    font-family: "Oswald", sans-serif; font-weight: 500; font-size: 30px; line-height: 40px;
    color: var(--ink); letter-spacing: 1px;
  }
  .product { font-weight: normal; }
  .product-name {
    position: absolute; font-family: "Lobster", cursive; color: var(--ink); line-height: 1;
    white-space: nowrap;
    text-shadow: 2px 2px 0 var(--gold-light), -1px -1px 0 var(--gold);
  }
  .name-first { left: 42px; top: 330px; font-size: 70px; transform: rotate(-6deg); transform-origin: left center; }
  .name-second { left: 446px; top: 282px; font-size: 62px; transform: rotate(-12deg); }
  .name-third { left: 160px; top: 420px; font-size: 90px; transform: rotate(-5deg); transform-origin: left center; }

  .type-box {
    position: absolute; left: 160px; top: 658px; width: 306px; height: 116px;
    border: 2px solid var(--ink);
    text-align: center; padding-top: 22px;
  }
  .type-name { font-family: "Oswald", sans-serif; font-weight: 600; font-size: 50px; color: var(--ink); line-height: 1; }
  .type-abv {
    position: absolute; left: 0; right: 0; bottom: -14px; margin: 0 auto; width: 110px;
    background: var(--label-mid); font-family: "Oranienbaum", serif; font-size: 19px; line-height: 26px; color: var(--ink);
  }
  .volume {
    position: absolute; left: 0; width: 620px; top: 868px; text-align: center;
    font-family: "Oranienbaum", serif; font-size: 44px; line-height: 60px; color: var(--ink);
  }
</style>
</head>
<body>
<div class="canvas">
  <section class="label">
    <div class="brush-band" role="img" aria-label="Sweeping pink and rose brush-stroke swirl"></div>
    <div class="ornament-top" role="img" aria-label="Gold filigree swirl ornament"></div>
    <div class="ornament-bottom" role="img" aria-label="Gold filigree swirl ornament"></div>

    <svg class="rules" width="620" height="960" viewBox="0 0 620 960" aria-hidden="true">
      <g stroke="var(--gold)" stroke-width="4" fill="none">
        <line x1="0" y1="76" x2="232" y2="76"/>
        <line x1="0" y1="100" x2="200" y2="100"/>
        <line x1="410" y1="760" x2="620" y2="760"/>
        <line x1="440" y1="784" x2="620" y2="784"/>
      </g>
      <g stroke="var(--ink)" stroke-width="3" fill="none">
        <line x1="0" y1="88" x2="232" y2="88"/>
        <line x1="410" y1="772" x2="620" y2="772"/>
      </g>
    </svg>

    <div class="brand">Tallow Crane</div>

    <h1 class="product">
      <span class="product-name name-first">Glittering</span>
      <span class="product-name name-second">Rose</span>
      <span class="product-name name-third">Raspberry</span>
    </h1>

    <div class="type-box">
      <div class="type-name">GIN LIQUER</div>
      <div class="type-abv">18.75%Vol</div>
    </div>

    <div class="volume">200ml</div>
  </section>
</div>
</body>
</html>
```